Looking for a cool, modern Cannabis Jar Label

I want you to come up with a better, modern look for a label.

I need it sized to 4” x 3” - I plan to print directly to label printer.

I want you to use Photoshop and deliver me a layered PSD file that I can edit and modify the information as needed..

The label information will need to include places for:
(1) Strain Name - most important part of label - larger font size than rest - example Kestrel Mist, PLV #7, Juniper Hollow
(2) Pricing - for Gram, 1/8, 1/4, 1/2. and Ounce
(3) Strain Designation (Hybrid, Indica or Sativa) - maybe color coded, different color for Indica v. Sativa, just an idea
(4) THC and CBD percentages - for example 23% THC and 0.05% CBD
(5) Farm name - a place where we can add the name/logo of the business that produced the product. example - Ovenrow Farms

I have attached a simple mockup showing the information.

I have also attached a few samples of labels we like to give you an idea of the look and feel we are going for.

I am wanting a very clean, modern, classy, readable look.The font will use is Gotham Font.

HI Everyone! Thank you for all of your designs. I am requesting an extension because I need more time to give adequate feedback to the designers. Thank you for your participation and all of your efforts! I will be making a decision soon!

• Gotham Font

• Thank you for your designs. I am sorry i have been slow in providing feedback, things have been really busy around here!
• I wanted to give some group general feedback. After reviewing all of the designs, there is a common theme among all of the designs that I would like to see changed.
• I would like to see the per gram pricing more prominent on the label. This is what most people are looking for when they are purchasing the product. So I would like to see this stand out from the other pricing tiers. As I think about it, they don't all need to be grouped together in a line. You could have the Per Gram pricing front and center some where and then the other pricing tiers grouped together somewhere else on the label.
• This is the order of importance of items on the label. Items at the the top of the list should be bigger than those below it.
• 1. Strain name
• 2. Pricing - being per gram the most important of all prices
• 3. THC/CBD percentages
• 4. Strain Type (indica, sativa, hybrid)
• 5. Farm name/logo
• When laying out these labels, they will be going on rounded jars and they will be on display. Think of jars with fancy labels in a candy store. They need to be eye catchy, appealing, but easy read.
• Thank you for all of your hard work, everyone is doing a great job.
• Best,
• Neta

```html
<!DOCTYPE html>
<html lang="en">
<head>
<meta charset="utf-8">
<title>Kestrel Mist – Jar Label</title>
<link href="https://fonts.googleapis.com/css2?family=Montserrat:wght@300;400;500;700;800&display=swap" rel="stylesheet">
<style>
  :root {
    --ink: #000000;
    --paper: #ffffff;
    --violet: #6200a3;
    --violet-text: #6a0dad;
    --lilac-1: #d6c0e6;
    --lilac-2: #c8a8df;
    --lilac-3: #bc95d9;
    --mist-1: #e9ddf3;
    --mist-2: #dac8ec;
    --tag: #d9c2ea;
  }
  html, body {
    margin: 0;
    padding: 0;
    width: 1200px;
    height: 917px;
    overflow: hidden;
    background: var(--paper);
  }
  .label {
    position: absolute;
    left: 0;
    top: 0;
    width: 1280px;
    height: 978px;
    transform: scale(0.9375);
    transform-origin: 0 0;
    font-family: "Montserrat", sans-serif;
  }
  .frame {
    position: absolute;
    left: 35px; top: 35px;
    width: 1200px; height: 900px;
    background: var(--ink);
  }
  .header-art {
    position: absolute;
    left: 0; top: 0;
  }
  .strain-name {
    position: absolute;
    left: 42px; top: 42px;
    width: 1113px; height: 280px;
    margin: 0;
    display: flex;
    flex-direction: column;
    align-items: center;
    justify-content: center;
    color: var(--violet-text);
    font-weight: 500;
    line-height: 1;
    text-shadow: 2px 3px 3px rgba(0,0,0,0.35);
  }
  .strain-name .primary { font-size: 118px; letter-spacing: 1px; }
  .strain-name .secondary { font-size: 92px; margin-top: 14px; letter-spacing: 1px; }
  .strain-type {
    position: absolute;
    left: 1155px; top: 62px;
    width: 73px;
    display: flex;
    flex-direction: column;
    align-items: center;
    color: var(--paper);
    font-size: 31px;
    font-weight: 400;
    line-height: 35.5px;
  }
  .pricing {
    position: absolute;
    left: 42px; top: 330px;
    width: 1186px;
    display: grid;
    grid-template-columns: 236px 238px 238px 238px 236px;
    grid-template-rows: 167px 168px;
  }
  .price, .unit {
    display: flex;
    align-items: center;
    justify-content: center;
  }
  .price { font-size: 76px; font-weight: 300; color: #111; }
  .unit { font-size: 104px; font-weight: 300; color: var(--violet-text); }
  .tier-a.price { background: var(--lilac-1); }
  .tier-b.price { background: var(--lilac-2); }
  .tier-c.price { background: var(--lilac-3); }
  .tier-a.unit { background: var(--paper); }
  .tier-b.unit { background: var(--mist-1); }
  .tier-c.unit { background: var(--mist-2); }
  .divider {
    position: absolute;
    left: 42px; top: 665px;
    width: 1186px; height: 10px;
    background: var(--violet);
  }
  .potency {
    position: absolute;
    top: 675px;
    height: 253px;
  }
  .potency.thc { left: 42px; width: 406px; }
  .potency.cbd { left: 455px; width: 403px; }
  .potency-sep {
    position: absolute;
    left: 448px; top: 675px;
    width: 7px; height: 253px;
    background: var(--violet);
  }
  .potency-name {
    height: 128px;
    display: flex; align-items: center; justify-content: center;
    color: var(--paper);
    font-size: 64px;
    font-weight: 800;
  }
  .potency-value {
    height: 125px;
    background: var(--violet);
    display: flex; align-items: center; justify-content: center;
    color: var(--paper);
    font-size: 96px;
    font-weight: 400;
    line-height: 1;
  }
  .potency-value sup { font-size: 46px; align-self: flex-start; margin-top: 22px; }
  .grower {
    position: absolute;
    left: 865px; top: 675px;
    width: 290px; height: 253px;
    background: var(--paper);
  }
  .grower-tag {
    height: 62px;
    background: var(--tag);
    display: flex; align-items: center; justify-content: center;
    font-size: 42px;
    font-weight: 300;
    color: #111;
    letter-spacing: 1px;
  }
  .grower-name {
    height: 191px;
    display: flex; align-items: center; justify-content: center;
    gap: 12px;
    color: #111;
    font-size: 30px;
    font-weight: 700;
    line-height: 1.1;
  }
  .grower-mark {
    width: 66px; height: 66px;
    border: 3px solid #111;
    border-radius: 50%;
    box-sizing: border-box;
    flex: none;
  }
  .pack-date {
    position: absolute;
    left: 1155px; top: 675px;
    width: 73px; height: 253px;
    display: flex; align-items: center; justify-content: center;
  }
  .pack-date span {
    transform: rotate(-90deg);
    color: var(--paper);
    font-size: 34px;
    font-weight: 400;
    white-space: nowrap;
    letter-spacing: 1px;
  }
</style>
</head>
<body>
<div class="label">
  <div class="frame"></div>

  <svg class="header-art" width="1280" height="330" viewBox="0 0 1280 330" aria-hidden="true">
    <rect x="42" y="42" width="1113" height="288" fill="#6200a3"/>
    <path d="M42 330 L42 300 C48 160 72 50 150 42 L1060 42 C1120 48 1140 150 1155 330 Z" fill="#000"/>
    <path d="M46 330 L46 300 C54 165 80 52 155 46 L1055 46 C1112 52 1130 155 1146 330 Z" fill="#fff"/>
  </svg>

  <h1 class="strain-name">
    <span class="primary">Kestrel Mist</span>
    <span class="secondary">Juniper Hollow</span>
  </h1>

  <div class="strain-type" aria-label="Hybrid">
    <span>H</span><span>Y</span><span>B</span><span>R</span><span>I</span><span>D</span>
  </div>

  <div class="pricing">
    <div class="price tier-a">$10</div>
    <div class="price tier-b">$35</div>
    <div class="price tier-c">$70</div>
    <div class="price tier-b">$140</div>
    <div class="price tier-a">$280</div>
    <div class="unit tier-a">g.</div>
    <div class="unit tier-b">1/8</div>
    <div class="unit tier-c">1/4</div>
    <div class="unit tier-b">1/2</div>
    <div class="unit tier-a">oz</div>
  </div>

  <div class="divider"></div>

  <div class="potency thc">
    <div class="potency-name">THC</div>
    <div class="potency-value">28<sup>%</sup></div>
  </div>
  <div class="potency-sep"></div>
  <div class="potency cbd">
    <div class="potency-name">CBD</div>
    <div class="potency-value">0.05<sup>%</sup></div>
  </div>

  <div class="grower">
    <div class="grower-tag">Grown by</div>
    <div class="grower-name">
      <span class="grower-mark"></span>
      <span>Ovenrow<br>Farms</span>
    </div>
  </div>

  <div class="pack-date"><span>27/08/18</span></div>
</div>
</body>
</html>
```